Web Infographic for Life Insurance

We need an infographic for our insurance site based on research commissioned previously. We have a report of statistics on the cost and coverage of life insurance in 1999 vs 2019. What we're looking for is an infographic that presents these statistics in an entertaining and informative way. Site is CoverWren.com
Target Market(s)
Americans ages 30-65 interested in life insurance.
Industry/Entity Type
Insurance
Number of Pages Required
1 page
Font styles to use
Sans Serif
Decorative
Colors
85cae6
faa54b
ffffff
86cfc6
Requirements
Must have
- Long vertical infographic readable on mobile devices
Nice to have
- Footnote references
Should not have
- Extremely small text
- Any brand logos or trademarked imagery other than for coverwren

```html
<!DOCTYPE html>
<html lang="en">
<head>
<meta charset="utf-8">
<title>CoverWren – Life Insurance by the Numbers</title>
<link rel="stylesheet" href="https://fonts.googleapis.com/css2?family=Poppins:wght@400;500;600&family=Roboto:wght@500;700&display=swap">
<style>
:root{
  --sky:#85cae6;
  --sky-deep:#6fb8da;
  --orange:#faa54b;
  --orange-deep:#f08a3c;
  --teal:#86cfc6;
  --white:#ffffff;
  --ink:#1c1c1c;
  --link-blue:#5aa6e0;
  --alert:#e0201b;
}
*{margin:0;padding:0;box-sizing:border-box}
html,body{width:1200px;height:3774px;overflow:hidden;background:var(--white)}
body{position:relative;font-family:"Poppins",sans-serif;color:var(--ink)}
.abs{position:absolute}
.bg-layer{position:absolute;left:0;top:0}
.brand{font-family:"Roboto",sans-serif;font-weight:500;font-size:46px;color:var(--ink);letter-spacing:-.5px}
.hero-title{left:110px;top:168px;width:520px;font-family:"Roboto",sans-serif;font-weight:500;font-size:35px;line-height:43px}
.hero-sub{left:110px;top:325px;width:460px;font-size:24px;line-height:32px;color:var(--white)}
.ph{position:absolute}
.down{position:absolute;left:582px;width:36px;height:36px}
.section-title{position:absolute;left:0;width:1200px;text-align:center;font-family:"Roboto",sans-serif;font-weight:500;font-size:35px;line-height:38px}
.stat-label{position:absolute;text-align:center;font-size:21px;font-weight:500}
.stat-value{position:absolute;text-align:center;font-size:28px;font-weight:600}
.tag{position:absolute;font-size:20px;font-weight:600;color:var(--orange-deep)}
.bullets{position:absolute;list-style:none}
.bullets li{position:relative;padding-left:30px;font-size:16px;line-height:28px;margin-bottom:18px;font-weight:500}
.bullets li::before{content:"";position:absolute;left:2px;top:8px;width:10px;height:10px;border-top:3px solid var(--sky-deep);border-right:3px solid var(--sky-deep);transform:rotate(45deg)}
.reason{position:absolute;width:200px;text-align:center}
.reason svg{display:block;margin:0 auto}
.reason p{font-size:20px;line-height:24px;font-weight:500;margin-top:12px}
</style>
</head>
<body>

<svg class="bg-layer" width="1200" height="3774" viewBox="0 0 1200 3774" aria-hidden="true">
  <defs>
    <linearGradient id="heroSky" x1="0" y1="0" x2="1" y2="1">
      <stop offset="0" stop-color="#9fd3ec"/>
      <stop offset="1" stop-color="#6fb8da"/>
    </linearGradient>
  </defs>
  <path d="M0,0 H1200 V330 C900,430 500,585 0,575 Z" fill="var(--orange)"/>
  <path d="M0,0 H1200 V318 C900,418 500,570 0,562 Z" fill="var(--teal)"/>
  <path d="M0,0 H1200 V305 C900,405 500,555 0,548 Z" fill="url(#heroSky)"/>
  <path d="M0,2070 C300,2030 450,1700 1200,1650 V2560 C850,2570 350,2610 0,2690 Z" fill="var(--teal)"/>
  <path d="M0,3774 C260,3660 700,3610 1200,3590 V3774 Z" fill="var(--teal)"/>
  <path d="M0,3774 C300,3690 720,3640 1200,3625 V3774 Z" fill="var(--sky)"/>
</svg>

<header>
  <div class="abs brand" style="left:110px;top:18px">coverwren</div>
  <h1 class="abs hero-title">We have a report of statistics on the cost and coverage of life insurance in 1999 vs 2019.</h1>
  <p class="abs hero-sub">Life can get complicated, insuring it shouldn’t be.</p>
  <div class="ph" role="img" aria-label="Insurance agent surrounded by a ring of coverage icons" style="left:628px;top:10px;width:500px;height:520px;border-radius:50%;background:radial-gradient(circle,#ffffff 0,#f3f3f3 45%,#fde2c4 70%,rgba(250,165,75,0) 72%)"></div>
</header>

<svg class="down" style="top:533px" viewBox="0 0 36 36" aria-hidden="true"><circle cx="18" cy="18" r="16" fill="none" stroke="#1c1c1c" stroke-width="2"/><path d="M18 9v17M11 19l7 7 7-7" fill="none" stroke="#1c1c1c" stroke-width="2.4"/></svg>

<section>
  <h2 class="abs" style="left:680px;top:585px;font-family:'Roboto',sans-serif;font-weight:500;font-size:37px">SUMMARY STATISTICS</h2>
  <div class="abs" style="left:940px;top:635px;font-size:29px;font-weight:600;color:var(--orange)">1992–1997</div>

  <div class="ph" role="img" aria-label="Illustration of people walking across a large insurance document" style="left:110px;top:670px;width:315px;height:200px;border-radius:8px;background:linear-gradient(135deg,#eeeeee,#cfcfcf)"></div>
  <div class="stat-label" style="left:147px;top:876px;width:300px">Type Term Premium</div>
  <div class="stat-value" style="left:147px;top:910px;width:300px">(3.62)</div>

  <div class="stat-label" style="left:510px;top:685px;width:300px">Length of policy</div>
  <div class="stat-value" style="left:510px;top:718px;width:300px">(2.27)</div>
  <div class="ph" role="img" aria-label="Grey pointing hand" style="left:565px;top:772px;width:192px;height:98px;border-radius:14px;background:linear-gradient(#b7b7b7,#8e8e8e)"></div>
  <svg class="abs" style="left:570px;top:860px" width="180" height="100" viewBox="0 0 180 100" aria-hidden="true">
    <path d="M18 0V92M11 84l7 8 7-8M162 0V92M155 84l7 8 7-8" fill="none" stroke="#333" stroke-width="2.5"/>
  </svg>
  <svg class="abs" style="left:465px;top:963px" width="36" height="36" viewBox="0 0 36 36" aria-hidden="true"><circle cx="18" cy="18" r="15" fill="none" stroke="#e0201b" stroke-width="2.5"/><path d="M8 28L28 8" stroke="#e0201b" stroke-width="2.5"/></svg>
  <div class="tag" style="left:517px;top:967px">Non-Smoker</div>
  <div class="tag" style="left:708px;top:967px">Male</div>
  <div class="ph" role="img" aria-label="Small man icon" style="left:770px;top:958px;width:28px;height:44px;border-radius:6px;background:#7fbfe0"></div>

  <div class="ph" role="img" aria-label="Stacked gold coins with a rising red arrow" style="left:910px;top:715px;width:180px;height:145px;border-radius:10px;background:linear-gradient(135deg,#f7c46b,#f06b4b)"></div>
  <div class="stat-label" style="left:830px;top:876px;width:300px">Real Amount of Policy</div>
  <div class="stat-value" style="left:830px;top:910px;width:300px">(132.97 )</div>
</section>

<svg class="down" style="top:1082px" viewBox="0 0 36 36" aria-hidden="true"><circle cx="18" cy="18" r="16" fill="none" stroke="#1c1c1c" stroke-width="2"/><path d="M18 9v17M11 19l7 7 7-7" fill="none" stroke="#1c1c1c" stroke-width="2.4"/></svg>

<section>
  <h2 class="section-title" style="top:1158px">Number of life insurance policy purchases in the<br>United States from 1998 to 2018 (in millions)</h2>
  <div class="ph" role="img" aria-label="Crowd of diverse adults standing together" style="left:100px;top:1275px;width:295px;height:155px;border-radius:8px;background:linear-gradient(90deg,#d7b48a,#7c8fb0,#c9553f)"></div>
  <svg class="abs" style="left:418px;top:1335px" width="44" height="40" viewBox="0 0 44 40" aria-hidden="true"><path d="M4 4l16 16-16 16M22 4l16 16-16 16" fill="none" stroke="#2f7fd6" stroke-width="6"/></svg>
  <div class="ph" role="img" aria-label="Grey map of the United States with coloured location markers" style="left:500px;top:1275px;width:300px;height:185px;border-radius:10px;background:#707070"></div>
  <svg class="abs" style="left:808px;top:1335px" width="44" height="40" viewBox="0 0 44 40" aria-hidden="true"><path d="M4 4l16 16-16 16M22 4l16 16-16 16" fill="none" stroke="#2f7fd6" stroke-width="6"/></svg>
  <div class="abs" style="left:937px;top:1340px;font-size:26px;font-weight:600">2.78%</div>
  <svg class="abs" style="left:1015px;top:1320px" width="26" height="44" viewBox="0 0 26 44" aria-hidden="true"><path d="M13 44V6M3 16L13 4l10 12" fill="none" stroke="#f0504b" stroke-width="4"/></svg>
  <p class="abs" style="left:867px;top:1376px;width:260px;font-size:15px;line-height:19px;color:var(--link-blue)">approximately 27.8 million life insurance policies were purchased in the United States.</p>
  <p class="abs" style="left:300px;top:1480px;width:600px;text-align:center;font-size:17px;line-height:21px;font-weight:500;color:var(--alert)">growth of the Internet has reduced term life prices by 8–15 percent.</p>
</section>

<svg class="down" style="top:1584px" viewBox="0 0 36 36" aria-hidden="true"><circle cx="18" cy="18" r="16" fill="none" stroke="#1c1c1c" stroke-width="2"/><path d="M18 9v17M11 19l7 7 7-7" fill="none" stroke="#1c1c1c" stroke-width="2.4"/></svg>

<section>
  <h2 class="abs" style="left:45px;top:1678px;font-family:'Roboto',sans-serif;font-weight:500;font-size:35px">Life insurance by the numbers</h2>
  <div class="ph" role="img" aria-label="Raised hands holding an umbrella, family, house, coins, car, graduation cap and policy document" style="left:0;top:1735px;width:520px;height:320px;background:linear-gradient(180deg,rgba(255,255,255,0),#dfe7ec 40%,#7a8a99)"></div>
  <ul class="bullets" style="left:582px;top:1682px;width:590px">
    <li>57%&nbsp; Percent of American adults who have life insurance‡</li>
    <li>32% Of American adults with life insurance, the percent who only have group coverage — which usually isn’t enough (and is rarely portable)‡</li>
    <li>10x to 12x&nbsp; The multiples of your annual income that most financial advisors recommend you need when buying life insurance for income replacement†</li>
    <li>50% Percent of life insurance policies are purchased via independent agents</li>
    <li>40% Percent of life insurance policies purchased via affiliated agents (meaning they only sell products for one insurance company)‡</li>
  </ul>
</section>

<svg class="down" style="top:2108px" viewBox="0 0 36 36" aria-hidden="true"><circle cx="18" cy="18" r="16" fill="none" stroke="#5a8f8a" stroke-width="2"/><path d="M18 9v17M11 19l7 7 7-7" fill="none" stroke="#5a8f8a" stroke-width="2.4"/></svg>

<section>
  <ul class="bullets" style="left:28px;top:2206px;width:570px">
    <li>6x–10x How much more permanent life insurance (like whole life insurance) costs vs. term life insurance†</li>
    <li>8% * Average percent increase in your insurance costs as you age, assuming your health stays the same†</li>
    <li>30% The average cost difference between sequential health ratings (preferred vs standard, for example)†</li>
    <li>2x to 3x How much rates for smokers cost vs. rates for nonsmokers (but a year after you quit smoking, most companies will offer you nonsmoker rates)†</li>
    <li>50% The average difference between the least expensive and most expensive rate for the same person across insurance companies†</li>
    <li>30% Percent difference between premiums for men and women (with women paying nearly 25% less than men, on average)†</li>
  </ul>
  <h2 class="abs" style="left:680px;top:2200px;font-family:'Roboto',sans-serif;font-weight:500;font-size:35px">The cost of life insurance</h2>
  <div class="ph" role="img" aria-label="Umbrella sheltering a dollar sign with family, heart, luggage, car and house icons" style="left:675px;top:2270px;width:505px;height:340px;border-radius:50% 50% 20px 20px/40% 40% 20px 20px;background:radial-gradient(circle at 50% 55%,#f2f2f2 0,#e4e4e4 45%,rgba(255,255,255,.6) 70%)"></div>
  <div class="abs" style="left:675px;top:2612px;width:505px;text-align:center;font-size:29px;font-weight:600;color:#444;letter-spacing:1px">INSURANCE</div>
</section>

<svg class="down" style="top:2731px" viewBox="0 0 36 36" aria-hidden="true"><circle cx="18" cy="18" r="16" fill="none" stroke="#1c1c1c" stroke-width="2"/><path d="M18 9v17M11 19l7 7 7-7" fill="none" stroke="#1c1c1c" stroke-width="2.4"/></svg>

<section>
  <h2 class="section-title" style="top:2834px">Top reasons for buying life insurance in the U.S.</h2>

  <div class="reason" style="left:82px;top:2928px"><svg width="136" height="136" viewBox="0 0 136 136"><circle cx="68" cy="68" r="64" fill="var(--teal)"/><path d="M68 132A64 64 0 0 1 68 4" fill="none" stroke="var(--sky-deep)" stroke-width="4"/><text x="68" y="82" text-anchor="middle" font-family="Poppins,sans-serif" font-size="38" font-weight="600" fill="var(--orange)">37%</text></svg><p>Income<br>replacement</p></div>
  <div class="reason" style="left:292px;top:2928px"><svg width="136" height="136" viewBox="0 0 136 136"><circle cx="68" cy="68" r="64" fill="var(--teal)"/><path d="M68 132A64 64 0 0 1 68 4" fill="none" stroke="var(--sky-deep)" stroke-width="4"/><text x="68" y="82" text-anchor="middle" font-family="Poppins,sans-serif" font-size="38" font-weight="600" fill="var(--orange)">30%</text></svg><p>Burial/final<br>expenses</p></div>
  <div class="reason" style="left:498px;top:2928px"><svg width="136" height="136" viewBox="0 0 136 136"><circle cx="68" cy="68" r="64" fill="var(--teal)"/><path d="M68 132A64 64 0 0 1 68 4" fill="none" stroke="var(--sky-deep)" stroke-width="4"/><text x="68" y="82" text-anchor="middle" font-family="Poppins,sans-serif" font-size="38" font-weight="600" fill="var(--orange)">28%</text></svg><p>Wealth<br>transfer</p></div>
  <div class="reason" style="left:708px;top:2928px"><svg width="136" height="136" viewBox="0 0 136 136"><circle cx="68" cy="68" r="64" fill="var(--teal)"/><path d="M68 132A64 64 0 0 1 68 4" fill="none" stroke="var(--sky-deep)" stroke-width="4"/><text x="68" y="82" text-anchor="middle" font-family="Poppins,sans-serif" font-size="38" font-weight="600" fill="var(--orange)">27%</text></svg><p>Pay off<br>mortgage</p></div>
  <div class="reason" style="left:917px;top:2928px"><svg width="136" height="136" viewBox="0 0 136 136"><circle cx="68" cy="68" r="64" fill="var(--teal)"/><path d="M68 132A64 64 0 0 1 68 4" fill="none" stroke="var(--sky-deep)" stroke-width="4"/><text x="68" y="82" text-anchor="middle" font-family="Poppins,sans-serif" font-size="38" font-weight="600" fill="var(--orange)">19%</text></svg><p>Replaced a<br>policy</p></div>

  <div class="reason" style="left:92px;top:3178px"><svg width="136" height="136" viewBox="0 0 136 136"><circle cx="68" cy="68" r="64" fill="var(--teal)"/><path d="M68 132A64 64 0 0 1 68 4" fill="none" stroke="var(--sky-deep)" stroke-width="4"/><text x="68" y="82" text-anchor="middle" font-family="Poppins,sans-serif" font-size="38" font-weight="600" fill="var(--orange)">17%</text></svg><p>Tax advantaged<br>save/invest</p></div>
  <div class="reason" style="left:290px;top:3178px"><svg width="136" height="136" viewBox="0 0 136 136"><circle cx="68" cy="68" r="64" fill="var(--teal)"/><path d="M68 132A64 64 0 0 1 68 4" fill="none" stroke="var(--sky-deep)" stroke-width="4"/><text x="68" y="82" text-anchor="middle" font-family="Poppins,sans-serif" font-size="38" font-weight="600" fill="var(--orange)">14%</text></svg><p>Estate taxes/<br>liquidity</p></div>
  <div class="reason" style="left:488px;top:3178px"><svg width="136" height="136" viewBox="0 0 136 136"><circle cx="68" cy="68" r="64" fill="var(--teal)"/><path d="M68 132A64 64 0 0 1 68 4" fill="none" stroke="var(--sky-deep)" stroke-width="4"/><text x="68" y="82" text-anchor="middle" font-family="Poppins,sans-serif" font-size="38" font-weight="600" fill="var(--orange)">14%</text></svg><p>Funds forcollege<br>education</p></div>
  <div class="reason" style="left:687px;top:3178px"><svg width="136" height="136" viewBox="0 0 136 136"><circle cx="68" cy="68" r="64" fill="var(--teal)"/><path d="M68 132A64 64 0 0 1 68 4" fill="none" stroke="var(--sky-deep)" stroke-width="4"/><text x="68" y="82" text-anchor="middle" font-family="Poppins,sans-serif" font-size="38" font-weight="600" fill="var(--orange)">13%</text></svg><p>Charitable<br>gift</p></div>
  <div class="reason" style="left:897px;top:3178px"><svg width="136" height="136" viewBox="0 0 136 136"><circle cx="68" cy="68" r="64" fill="var(--teal)"/><path d="M68 132A64 64 0 0 1 68 4" fill="none" stroke="var(--sky-deep)" stroke-width="4"/><text x="68" y="82" text-anchor="middle" font-family="Poppins,sans-serif" font-size="38" font-weight="600" fill="var(--orange)">8%</text></svg><p>Supplement group<br>coverage</p></div>

  <div class="reason" style="left:76px;top:3428px"><svg width="136" height="136" viewBox="0 0 136 136"><circle cx="68" cy="68" r="64" fill="var(--teal)"/><path d="M68 132A64 64 0 0 1 68 4" fill="none" stroke="var(--sky-deep)" stroke-width="4"/><text x="68" y="82" text-anchor="middle" font-family="Poppins,sans-serif" font-size="38" font-weight="600" fill="var(--orange)">8%</text></svg><p>Business<br>purposes</p></div>
</section>

<footer>
  <p class="abs" style="left:118px;top:3712px;font-size:14px;color:#333">Copyright © 2020. All Rights Reserved</p>
  <div class="abs brand" style="left:836px;top:3670px">coverwren</div>
</footer>

</body>
</html>
```